Coastline Premier Retreats Business Card Design

Design a business card for Coastline Premier Retreats. Look at the website for colors and reference. Card should have logo, name, title, office number, mobile number, email, URL and a tagline like, "Luxury Hotel & Resort Email Marketing" (This might change).

https://www.coastlinepremierretreats.example

The rest I will leave up to your imagination.

Contact Information for Business Card

Logo, name, title, office number, mobile number, email, URL and a tagline like, "Luxury Hotel & Resort Email Marketing" (This might change).

```html
<!DOCTYPE html>
<html lang="en">
<head>
<meta charset="utf-8">
<title>Coastline Premier Retreats – Business Card</title>
<link href="https://fonts.googleapis.com/css2?family=Arimo:wght@400;700&display=swap" rel="stylesheet">
<style>
  :root {
    --stage: #2b2b2b;
    --card: #1c1c1c;
    --card-back: #161616;
    --accent: #f07d19;
    --text: #f2f2f2;
    --muted: #d8d8d8;
    --emboss: #2a2a2a;
  }
  * { margin: 0; padding: 0; box-sizing: border-box; }
  html, body { width: 1200px; height: 915px; overflow: hidden; }
  body {
    background: var(--stage);
    font-family: "Arimo", Arial, sans-serif;
    position: relative;
  }
  .card {
    position: absolute;
    left: 250px;
    width: 700px;
    height: 400px;
    border-radius: 22px;
    overflow: hidden;
  }
  .card--back { top: 40px; background: var(--card-back); }
  .card--front { top: 475px; background: var(--card); color: var(--text); }

  /* back side */
  .back-name {
    position: absolute;
    left: 0; right: 0; top: 170px;
    text-align: center;
    font-size: 46px;
    font-weight: 700;
    color: var(--emboss);
    letter-spacing: 1px;
  }

  /* front side */
  .brand {
    position: absolute;
    left: 40px; top: 168px;
    width: 290px;
    display: flex; align-items: center; gap: 10px;
  }
  .brand__square { width: 16px; height: 16px; background: var(--accent); flex: none; }
  .brand__name {
    font-size: 18px; font-weight: 700; color: var(--text);
    letter-spacing: 0.3px; white-space: nowrap;
  }
  .divider {
    position: absolute;
    left: 360px; top: 60px;
    width: 2px; height: 220px;
    background: var(--accent);
  }
  .details { position: absolute; left: 385px; top: 62px; width: 300px; }
  .details__name {
    font-size: 26px; font-weight: 700; color: var(--accent);
    letter-spacing: 0.5px; line-height: 1;
  }
  .details__title { font-size: 15px; margin-top: 6px; color: var(--muted); }
  .details__address { font-size: 14px; line-height: 1.35; margin-top: 14px; color: var(--muted); }
  .contact { list-style: none; margin-top: 12px; }
  .contact li {
    display: flex; align-items: center; gap: 8px;
    font-size: 13.5px; line-height: 1.55; color: var(--muted); white-space: nowrap;
  }
  .contact svg { width: 12px; height: 12px; flex: none; }
  .tagline {
    position: absolute;
    left: 0; right: 0; bottom: 38px;
    text-align: center;
    font-size: 17px; color: var(--text); letter-spacing: 0.3px;
  }
</style>
</head>
<body>
  <section class="card card--back" aria-label="Card back">
    <p class="back-name">Coastline Premier Retreats</p>
  </section>

  <section class="card card--front" aria-label="Card front">
    <div class="brand">
      <span class="brand__square"></span>
      <span class="brand__name">Coastline Premier Retreats</span>
    </div>

    <div class="divider"></div>

    <div class="details">
      <h1 class="details__name">DANIEL REYES</h1>
      <p class="details__title">CEO/Founder</p>
      <p class="details__address">PO Box 48, 210 Harbor Rd<br>Seaview, ST 00000</p>
      <ul class="contact">
        <li>
          <svg viewBox="0 0 12 12"><rect x="3" y="0.5" width="6" height="11" rx="1" fill="none" stroke="#f07d19" stroke-width="1.2"/><circle cx="6" cy="9.5" r="0.7" fill="#f07d19"/></svg>
          555.014.2200
        </li>
        <li>
          <svg viewBox="0 0 12 12"><path d="M1 5 Q6 1 11 5 L9.5 6.5 L8 5.2 L4 5.2 L2.5 6.5 Z M3 7 H9 V11 H3 Z" fill="#f07d19"/></svg>
          +34 600 000 123
        </li>
        <li>
          <svg viewBox="0 0 12 12"><rect x="0.5" y="2.5" width="11" height="7.5" fill="#f07d19"/><path d="M0.5 2.5 L6 7 L11.5 2.5" fill="none" stroke="#1c1c1c" stroke-width="1"/></svg>
          info@coastlinepremierretreats.example
        </li>
        <li>
          <svg viewBox="0 0 12 12"><circle cx="6" cy="6" r="5.5" fill="#f07d19"/><path d="M0.5 6 H11.5 M6 0.5 V11.5" stroke="#1c1c1c" stroke-width="0.8"/></svg>
          www.coastlinepremierretreats.example
        </li>
      </ul>
    </div>

    <p class="tagline">Luxury Hotel &amp; Resort Email Marketing</p>
  </section>
</body>
</html>
```